Corporate Business Card

Very professional, Modern, Not to busy, include phone address email, website
(253) 617-4930, 18761 52nd Avenue S, Kent, WA 98047, martin@plumlinegroup.com, varkoworks.com

Target Market(s)

Manufacturing

Industry/Entity Type

Aero, machining, manufacturing, Off road racing

Contact Information for Business Card

Phone, address email, website

```html
<!DOCTYPE html>
<html lang="en">
<head>
<meta charset="utf-8">
<title>Varko Industries – Business Card</title>
<link rel="stylesheet" href="https://fonts.googleapis.com/css2?family=Roboto:wght@400;500;700&family=Exo+2:wght@800&display=swap">
<style>
  :root {
    --navy: #2a3a6b;
    --navy-deep: #253564;
    --red: #c0242b;
    --paper: #ededed;
    --paper-shade: #dedede;
    --backdrop: #2b2b2b;
    --white: #f2f2f2;
  }
  * { box-sizing: border-box; margin: 0; padding: 0; }
  html, body { width: 1200px; height: 1138px; overflow: hidden; }
  body {
    background: var(--backdrop);
    font-family: "Roboto", Arial, sans-serif;
    position: relative;
  }
  .card {
    position: absolute;
    border-radius: 14px;
    overflow: hidden;
  }
  /* Front */
  .card-front {
    left: 274px; top: 186px; width: 623px; height: 376px;
    background: var(--navy);
  }
  .brand-name {
    position: absolute;
    left: 0; right: 0; top: 140px;
    text-align: center;
    font-weight: 700;
    font-size: 46px;
    letter-spacing: 2px;
    color: var(--white);
  }
  .front-web {
    position: absolute;
    left: 0; right: 0; top: 326px;
    text-align: center;
    font-size: 16px;
    letter-spacing: 11px;
    color: var(--white);
  }
  .front-web .accent { color: var(--red); }
  /* Back */
  .card-back {
    left: 276px; top: 608px; width: 618px; height: 374px;
    background: linear-gradient(180deg, var(--paper) 0%, var(--paper) 55%, var(--paper-shade) 100%);
  }
  .person-name {
    position: absolute;
    left: 26px; top: 75px;
    font-family: "Exo 2", "Roboto", sans-serif;
    font-weight: 800;
    font-size: 25px;
    color: var(--navy);
    letter-spacing: 0.5px;
  }
  .person-name .surname { color: var(--red); }
  .contact-band {
    position: absolute;
    left: 0; top: 138px; width: 302px; height: 98px;
    background: var(--navy);
    padding-top: 14px;
  }
  .contact-line {
    display: flex; align-items: center;
    height: 24px;
    padding-left: 26px;
    font-size: 17px;
    color: var(--white);
  }
  .contact-line svg { width: 16px; height: 14px; margin-right: 16px; fill: var(--red); }
  .back-brand {
    position: absolute;
    left: 317px; top: 170px; width: 275px;
    text-align: center;
    font-weight: 700;
    font-size: 27px;
    letter-spacing: 1px;
    color: var(--navy);
  }
  .edge-bar {
    position: absolute;
    left: 608px; top: 138px; width: 10px; height: 98px;
    background: var(--red);
  }
  .address {
    position: absolute;
    left: 26px; top: 257px;
    font-size: 17px;
    line-height: 24px;
    color: var(--navy);
  }
</style>
</head>
<body>
  <section class="card card-front">
    <div class="brand-name">VARKO INDUSTRIES</div>
    <div class="front-web">www.varko<span class="accent">works</span>.com</div>
  </section>

  <section class="card card-back">
    <div class="person-name">MARTIN <span class="surname">HALE</span></div>
    <div class="contact-band">
      <div class="contact-line">
        <svg viewBox="0 0 16 14" aria-hidden="true"><path d="M1 4c0-2 3-3 7-3s7 1 7 3v1h-4V4H5v1H1z"/><path d="M3 6h10l2 7H1z"/></svg>
        (253) 617-4930
      </div>
      <div class="contact-line">
        <svg viewBox="0 0 16 14" aria-hidden="true"><path d="M0 2h16v10H0z M1.5 3.2 8 8l6.5-4.8" fill="var(--red)"/><path d="M1 3l7 5 7-5" fill="none" stroke="var(--navy)" stroke-width="1.4"/></svg>
        martin@plumlinegroup.com
      </div>
      <div class="contact-line">
        <svg viewBox="0 0 16 14" aria-hidden="true"><circle cx="8" cy="7" r="6.5" fill="none" stroke="var(--red)" stroke-width="1.4"/><path d="M1.5 7h13M8 .5v13" stroke="var(--red)" stroke-width="1.2"/><ellipse cx="8" cy="7" rx="3" ry="6.5" fill="none" stroke="var(--red)" stroke-width="1.2"/></svg>
        www.varkoworks.com
      </div>
    </div>
    <div class="back-brand">VARKO INDUSTRIES</div>
    <div class="edge-bar"></div>
    <address class="address" style="font-style:normal">18761 52nd Avenue S,<br>Kent, WA 98047</address>
  </section>
</body>
</html>
```